IT Company requires new Business Card design.

Over the years we have had a few different business card designs. We are now due for new cards across the board for all staff. We felt this would be a good time to start fresh with a new design. Our traditional card simply had our details on the front, and a list of services on the back. We don't particularly need the list of services, we have had cards where the only thing on the rear of the card was our logo.
Feel free to be creative, we would like our tag line "Complete IT Management" to appear at some point, doesn't necessarily have to be with the logo.
I have attached samples and drafts of various previous cards we have used over the years.

```html
<!DOCTYPE html>
<html lang="en">
<head>
<meta charset="utf-8">
<title>Harbor Systems – Business Card</title>
<link href="https://fonts.googleapis.com/css2?family=Open+Sans:wght@400;600;800&display=swap" rel="stylesheet">
<style>
  :root{
    --slate:#5f7180;
    --ink:#3a3f44;
    --card:#ffffff;
    --backdrop:#e6e6ec;
    --rule:#8a97a2;
  }
  *{box-sizing:border-box;margin:0;padding:0}
  html,body{width:1200px;height:987px;overflow:hidden}
  body{
    background:var(--backdrop);
    font-family:"Open Sans",Arial,sans-serif;
    color:var(--ink);
    display:flex;flex-direction:column;align-items:center;justify-content:center;gap:40px;
  }
  .card{
    width:760px;height:434px;background:var(--card);
    border-radius:26px;position:relative;
    box-shadow:0 6px 18px rgba(0,0,0,.12);
  }
  /* front */
  .brand{position:absolute;left:52px;top:150px;width:310px}
  .brand-row{display:flex;align-items:center;gap:14px}
  .brand-mark{width:34px;height:34px;background:var(--slate)}
  .brand-name{font-weight:800;font-size:34px;line-height:1.02;color:var(--slate);text-transform:uppercase}
  .tagline{margin-top:10px;font-size:12px;letter-spacing:4px;color:var(--slate);text-transform:uppercase;padding-left:48px}
  .divider{position:absolute;left:392px;top:70px;width:2px;height:300px;background:var(--rule)}
  .divider::before{content:"";position:absolute;left:-2px;top:0;width:6px;height:46px;background:var(--slate)}
  .contact{position:absolute;left:420px;top:70px;right:30px}
  .person-name{font-weight:800;font-size:25px;color:var(--slate);line-height:1.1}
  .person-role{font-size:19px;color:var(--ink);margin-bottom:14px}
  .contact-list{list-style:none}
  .contact-list li{display:flex;align-items:center;gap:10px;font-size:18px;line-height:28px}
  .contact-list svg{width:17px;height:17px;flex:none;fill:var(--slate)}
  .address{margin-top:10px;font-size:18px;line-height:26px}
  /* back */
  .back-brand{position:absolute;left:0;right:0;top:120px;display:flex;justify-content:center;align-items:center;gap:22px}
  .back-brand .brand-mark{width:70px;height:70px}
  .back-brand .brand-name{font-size:64px}
  .back-url{position:absolute;left:0;right:0;bottom:70px;text-align:center;font-size:20px;letter-spacing:1.5px;color:var(--ink)}
</style>
</head>
<body>

<section class="card card-front">
  <div class="brand">
    <div class="brand-row">
      <span class="brand-mark"></span>
      <span class="brand-name">Harbor<br>Systems</span>
    </div>
    <p class="tagline">Complete IT Management</p>
  </div>

  <div class="divider"></div>

  <div class="contact">
    <p class="person-name">Martin Hale</p>
    <p class="person-role">Operation Manager</p>
    <ul class="contact-list">
      <li><svg viewBox="0 0 20 20"><path d="M5 2l3 4-2 2c1 2 3 4 5 5l2-2 4 3-2 3C9 17 3 11 2 4z"/></svg>08 5550 1840</li>
      <li><svg viewBox="0 0 20 20"><path d="M6 1h8v18H6zM8 3v11h4V3z"/></svg>0400 555 718</li>
      <li><svg viewBox="0 0 20 20"><path d="M5 2h9v5H5zM2 8h16v8H2zM5 14h10v5H5z"/></svg>08 5550 1840</li>
      <li><svg viewBox="0 0 20 20"><path d="M1 4h18v12H1zM3 6l7 5 7-5v-1l-7 5-7-5z"/></svg>martin@harborsystems.com.au</li>
      <li><svg viewBox="0 0 20 20"><path d="M10 1a9 9 0 100 18 9 9 0 000-18zm0 2c1 1 2 3 2 7s-1 6-2 7c-1-1-2-3-2-7s1-6 2-7zM2 9h16v2H2z"/></svg>www.harborsystems.com.au</li>
    </ul>
    <p class="address">Unit 4 12 Quarry Lane<br>Bayview WA 6000</p>
  </div>
</section>

<section class="card card-back">
  <div class="back-brand">
    <span class="brand-mark"></span>
    <span class="brand-name">Harbor<br>Systems</span>
  </div>
  <p class="back-url">www.harborsystems.com.au</p>
</section>

</body>
</html>
```